New template needed for Joomla 3.2 website

We are a mortgage origination company based in Johannesburg, South Africa and require a sleek, modern & professional look for our website.
The website is complete and your template should accommodate all pages on the site (there are not many) and be ready for Joomla implementation.
Our website can be viewed at www.keystonebondhub.co.za
Target Market(s)
We are targeting consumers who require mortgage finance to buy real estate. There is no particular demographic, except that we cater to South African home buyers exclusively!
Requirements
Must have
- It must look professional and modern.
Take a look at competitor websites:
www.ziva.co.za
www.pkbondfinder.com
http://www.tallwavegroup.co.za/bondpeak/
http://www.ridgeloan.co.za/
We want to beat the competition !!
Nice to have
- Website should blend with company logo and play on the symbol in the logo.
I want more of a people / photo element to the template. It needs to make us seem "tangible"

```html
<!DOCTYPE html>
<html lang="en">
<head>
<meta charset="utf-8">
<title>Keystone Home Loans</title>
<link href="https://fonts.googleapis.com/css2?family=Roboto:wght@300;400;500;700&display=swap" rel="stylesheet">
<style>
:root{
  --brand:#1a63b5;
  --brand-dark:#1558a6;
  --brand-light:#3b7fcb;
  --title:#1b64b3;
  --text:#6a6a6a;
  --body-dark:#4a4a4a;
  --band:#efefef;
  --btn:#3c3c3c;
  --white:#ffffff;
}
*{box-sizing:border-box;margin:0;padding:0}
html,body{width:854px;height:1200px;overflow:hidden;background:var(--white)}
body{position:relative;font-family:"Roboto",Arial,sans-serif;color:var(--text)}
.abs{position:absolute}
/* header */
.brand{left:120px;top:26px;display:flex;align-items:center;gap:9px}
.brand-dot{width:30px;height:30px;border-radius:50%;background:var(--brand)}
.brand-name{font-size:19px;font-weight:500;color:var(--brand);letter-spacing:.2px}
.call{right:120px;top:34px;font-size:15px;color:var(--brand)}
/* nav */
.nav{left:0;top:82px;width:854px;height:42px;background:linear-gradient(#2a73c4,var(--brand-dark));display:flex;padding-left:120px}
.nav a{color:var(--white);text-decoration:none;font-size:10.5px;line-height:42px;padding:0 11px}
.nav a.active{background:rgba(255,255,255,.2);width:52px;text-align:center;padding:0}
.nav a:nth-child(2){padding-left:9px}
/* hero */
.hero{left:0;top:124px;width:854px;height:404px;background:linear-gradient(180deg,#6e6e6e 0%,#8f8f8f 45%,#c9c9c9 70%,#e6e6e6 100%)}
.hero-photo{left:480px;top:188px;width:290px;height:300px;background:linear-gradient(160deg,#e8e3c8,#f2f2f2 40%,#dcdcdc);border-radius:4px;opacity:.8}
.hero-title{left:147px;top:190px;font-size:21px;font-weight:500;color:var(--white)}
.hero-list{left:148px;top:236px;list-style:none}
.hero-list li{display:flex;align-items:center;gap:9px;font-size:18px;font-weight:500;color:var(--white);height:43px}
.arrow{top:326px}
/* features */
.feature{width:140px;text-align:center}
.feature .icon{width:62px;height:62px;border-radius:50%;background:radial-gradient(circle at 40% 30%,var(--brand-light),var(--brand-dark));margin:0 auto;display:flex;align-items:center;justify-content:center}
.feature h3{font-size:12.5px;font-weight:500;color:var(--title);margin-top:20px;letter-spacing:.3px}
.feature p{font-size:10px;line-height:15.5px;margin-top:8px;height:31px;overflow:hidden;white-space:nowrap}
.btn{display:inline-block;width:86px;height:25px;line-height:23px;background:linear-gradient(#555,var(--btn));border:1px solid #222;border-radius:2px;color:var(--white);font-size:9px;text-align:center;margin-top:7px}
/* why band */
.why{left:0;top:756px;width:854px;height:204px;background:var(--band)}
.why-img{left:122px;top:770px;width:228px;height:165px;background:linear-gradient(#e9e3dc,#c9bdb3 55%,#a6542f 56%,#d8d0c8);border-radius:3px}
.why-title{left:374px;top:790px;font-size:16px;font-weight:400;color:var(--title)}
.why-text{left:377px;top:818px;width:352px;font-size:10.5px;line-height:21.5px;color:var(--body-dark);text-align:justify}
/* lower */
.sec-title{font-size:13px;font-weight:400;color:var(--title)}
.ref-text{left:120px;top:1007px;width:345px;font-size:11px;line-height:16px}
.card-img{background:linear-gradient(135deg,#3aa3e3,#1a4f9c);border-radius:3px}
.shop-img{background:linear-gradient(#f4f4f4,#e4e4e4)}
.badge{left:686px;top:1009px;width:42px;height:26px;background:var(--brand-dark);border-radius:2px}
/* footer */
.footer{left:0;top:1094px;width:854px;height:106px;background:var(--brand)}
.footer-links{left:124px;top:1135px;font-size:8.5px;color:var(--white)}
.copy{left:122px;top:1155px;font-size:8.5px;color:var(--white)}
.follow{left:604px;top:1126px;font-size:10px;color:var(--white)}
.social{left:604px;top:1145px;display:flex;gap:7px}
.social span{width:20px;height:20px;background:#dfe7f1;border-radius:2px}
</style>
</head>
<body>

<header>
  <div class="abs brand">
    <span class="brand-dot"></span>
    <span class="brand-name">Keystone Home Loans</span>
  </div>
  <div class="abs call">CALL : ( 010 ) 555 0148</div>
</header>

<nav class="abs nav">
  <a class="active" href="#">HOME</a>
  <a href="#">ABOUT KEYSTONE</a>
  <a href="#">IMPORTANT INFORMATION</a>
  <a href="#">HOMELOAN CALCULATORS</a>
  <a href="#">APPLY ON-LINE</a>
  <a href="#">CONTACT KEYSTONE</a>
</nav>

<section class="abs hero" role="img" aria-label="Photo of a small white model house with a banknote roof beside a stack of coins"></section>
<div class="abs hero-photo" role="img" aria-label="Model house with banknote roof"></div>
<h1 class="abs hero-title">FAST HOMELOANS . GREAT SERVICE !</h1>
<ul class="abs hero-list">
  <li><svg width="18" height="18" viewBox="0 0 18 18"><circle cx="9" cy="9" r="9" fill="#fff"/><path d="M5 9.3l2.8 2.7L13 6.5" fill="none" stroke="#8a8a8a" stroke-width="2.2"/></svg>100% FREE OF CHARGE</li>
  <li><svg width="18" height="18" viewBox="0 0 18 18"><circle cx="9" cy="9" r="9" fill="#fff"/><path d="M5 9.3l2.8 2.7L13 6.5" fill="none" stroke="#8a8a8a" stroke-width="2.2"/></svg>EXCEPTIONAL SERVICE</li>
  <li><svg width="18" height="18" viewBox="0 0 18 18"><circle cx="9" cy="9" r="9" fill="#fff"/><path d="M5 9.3l2.8 2.7L13 6.5" fill="none" stroke="#8a8a8a" stroke-width="2.2"/></svg>CREDIT HELP</li>
</ul>
<svg class="abs arrow" style="left:40px" width="22" height="34" viewBox="0 0 22 34"><path d="M18 3L5 17l13 14" fill="none" stroke="#fff" stroke-width="4"/></svg>
<svg class="abs arrow" style="left:790px" width="22" height="34" viewBox="0 0 22 34"><path d="M4 3l13 14L4 31" fill="none" stroke="#fff" stroke-width="4"/></svg>

<section>
  <div class="abs feature" style="left:122px;top:558px">
    <div class="icon"><svg width="24" height="22" viewBox="0 0 24 22"><path d="M12 1L1 11h3v10h6v-6h4v6h6V11h3z" fill="#fff"/></svg></div>
    <h3>REFERRAL PROGRAM</h3>
    <p>Click on the button below to<br>join our lead referal program</p>
    <span class="btn">JOIN TODAY</span>
  </div>
  <div class="abs feature" style="left:277px;top:557px">
    <div class="icon"><svg width="30" height="30" viewBox="0 0 30 30"><circle cx="11" cy="11" r="6" fill="none" stroke="#fff" stroke-width="4" stroke-dasharray="3 2"/><circle cx="22" cy="8" r="3.5" fill="none" stroke="#fff" stroke-width="2.5"/><circle cx="12" cy="23" r="3.5" fill="none" stroke="#fff" stroke-width="2.5"/></svg></div>
    <h3>GET PRE QUALIFIED</h3>
    <p>Our experienced consultants<br>would be happy to prequalify</p>
    <span class="btn">APPLY NOW</span>
  </div>
  <div class="abs feature" style="left:435px;top:557px">
    <div class="icon"><svg width="22" height="26" viewBox="0 0 22 26"><path d="M11 1l9 4v7c0 6-4 10-9 13C6 22 2 18 2 12V5z" fill="#fff"/><text x="11" y="17" font-size="11" font-weight="700" text-anchor="middle" fill="#1a63b5" font-family="Roboto,sans-serif">?</text></svg></div>
    <h3>ASK A QUESTION</h3>
    <p>Ask an experienced consul-<br>tant to answer all your ques-</p>
    <span class="btn">ASK NOW</span>
  </div>
  <div class="abs feature" style="left:589px;top:559px">
    <div class="icon"><svg width="22" height="26" viewBox="0 0 22 26"><rect x="1" y="1" width="20" height="24" rx="2" fill="none" stroke="#fff" stroke-width="2"/><rect x="5" y="5" width="12" height="4" fill="#fff"/><rect x="5" y="12" width="5" height="9" fill="#fff"/><rect x="12" y="12" width="5" height="4" fill="#fff"/><rect x="12" y="17" width="5" height="4" fill="#fff"/></svg></div>
    <h3>CALCULATORS</h3>
    <p>Find out what you can afford<br>with our convenient finance</p>
    <span class="btn">CALCULATE</span>
  </div>
</section>

<section class="abs why"></section>
<div class="abs why-img" role="img" aria-label="Illustration of a white two-storey house with a red roof"></div>
<h2 class="abs why-title">WHY KEYSTONEHOMELOANS</h2>
<p class="abs why-text">Lorem Ipsum is simply dummy text of the printing and typesetting industry. Lorem Ipsum has been the industry's standard dummy text ever since the 1500s, when an unknown printer took a galley of type &nbsp;remaining essentially unchanged.</p>
<span class="abs btn" style="left:377px;top:905px">READ MORE</span>

<h2 class="abs sec-title" style="left:120px;top:980px">KEYSTONE LEAD REFERRAL PROGRAM</h2>
<p class="abs ref-text">We invite members of the public, estate agents, attorneys, property developers and all other property professionals to refer leads to us. Why not join our referal program and earn money for every successful lead. It pays!</p>
<h2 class="abs sec-title" style="left:497px;top:982px;font-size:12px">KEYSTONE CREDIT CARD</h2>
<div class="abs card-img" style="left:502px;top:1006px;width:78px;height:68px" role="img" aria-label="Two blue bank cards"></div>
<div class="abs shop-img" style="left:594px;top:1006px;width:70px;height:72px" role="img" aria-label="Photo of a shopper carrying colourful bags"></div>
<div class="abs badge"></div>

<footer class="abs footer"></footer>
<div class="abs footer-links">Privacy Policy | Terms Conditions | Sitemap | Contact Us</div>
<div class="abs copy">Copyright © 2014 &nbsp;All Rights Reserved</div>
<div class="abs follow">FOLLOW US</div>
<div class="abs social"><span></span><span></span><span></span><span></span><span></span></div>

</body>
</html>
```